Print design needed to improve the layout and look of some existing documents

We need someone to take a couple of existing documents that we have and make them look much better using our existing logo and corporate colors etc. We require these to be delivered in a format that will allow our staff to edit the content as necessary via Microsoft word for conversion once finalized into a PDF. Ideally, we will also be able to use this as a newsletter template or for other documents that might be required in our business. www.corvelleadvisory.com.au
Updates

Target Market(s)

Business owners, executives, retirees

Industry/Entity Type

Financial Service

Font styles to use
Serif

Requirements
Must have
• Design that uses our existing branding and colors. It also needs to be ina form that we can edit the content / update easily. Ideally the format / layout could also be used for other documents such as short newsletters etc.
Nice to have
• Fresh, simple and crisp. Very professional looking.
Should not have
• strange fonts, weird layouts.

```html
<!DOCTYPE html>
<html lang="en">
<head>
<meta charset="utf-8">
<title>Corvelle Advisory – Financial Services Guide</title>
<link rel="stylesheet" href="https://fonts.googleapis.com/css2?family=Open+Sans:wght@400;600;700&family=Ubuntu:wght@500;700&display=swap">
<style>
  :root{
    --backdrop:#e7e7e9;
    --paper:#ffffff;
    --panel:#f5f5f5;
    --card:#e6e6e8;
    --ink:#4a4a4a;
    --brand-blue:#1597d5;
    --brand-green:#6cb42c;
    --name-box:#3c3c3e;
  }
  *{box-sizing:border-box;margin:0;padding:0}
  html,body{width:1200px;height:793px;overflow:hidden;background:var(--backdrop)}
  body{position:relative;font-family:"Open Sans",Arial,sans-serif;color:var(--ink)}
  .page{position:absolute;top:34px;width:518px;height:730px;background:var(--paper)}
  .page--left{left:72px}
  .page--right{left:618px}
  .panel{position:absolute;left:17px;top:20px;width:484px;height:691px;background:var(--panel)}
  .brand{position:absolute;left:20px;top:24px;display:flex;align-items:center;gap:8px}
  .brand__mark{width:16px;height:22px;background:var(--brand-blue)}
  .brand__name{font-size:19px;font-weight:400;letter-spacing:.5px;color:#55575a;line-height:1}
  .section-title{position:absolute;top:66px;height:18px;display:flex;align-items:center;gap:6px;
    font-family:"Ubuntu",sans-serif;font-weight:500;font-size:13px;line-height:18px;color:var(--brand-blue)}
  .section-title svg{width:14px;height:14px;flex:none}
  .card{position:absolute;width:209px;background:var(--card)}
  .card__head{display:flex;height:76px}
  .card__photo{width:112px;height:76px}
  .card__name{flex:1;background:var(--name-box);color:#fff;font-family:"Ubuntu",sans-serif;
    font-weight:700;font-size:12.5px;display:flex;align-items:center;justify-content:center}
  .card__body{padding:9px 6px 0 6px}
  .text{font-size:8.7px;line-height:11.5px;color:var(--ink)}
  .text p{margin-bottom:11.5px}
  .fees{line-height:12.5px}
  .fees p{margin-bottom:10px}
  .fees h4{font-size:9px;line-height:12.5px;font-weight:600;color:var(--brand-blue);margin:4px 0 5px}
  .footer{position:absolute;left:17px;top:689px;width:484px;height:22px;background:var(--brand-blue);
    display:flex;align-items:center;color:#fff;font-size:6.4px;padding-left:19px}
  .footer__page{position:absolute;right:0;top:0;width:46px;height:22px;background:var(--brand-green);
    font-family:"Ubuntu",sans-serif;font-weight:700;font-size:11px;display:flex;align-items:center;justify-content:center}
  .column{position:absolute;top:106px}
</style>
</head>
<body>

<section class="page page--left">
  <div class="panel">
    <div class="brand"><span class="brand__mark"></span><span class="brand__name">CORVELLE ADVISORY</span></div>
    <h2 class="section-title" style="left:19px">
      <svg viewBox="0 0 14 14"><circle cx="7" cy="7" r="6.2" fill="none" stroke="var(--brand-green)" stroke-width="1.2"/><path d="M6 4.3 8.6 7 6 9.7" fill="none" stroke="var(--brand-green)" stroke-width="1.3"/></svg>
      Your Financial Advisers
    </h2>

    <article class="card" style="left:20px;top:96px;height:280px">
      <div class="card__head">
        <div class="card__photo" role="img" aria-label="Portrait photo of Martin Hale outdoors" style="background:linear-gradient(160deg,#9fb4c4,#6f8a6a 60%,#2f3e58)"></div>
        <div class="card__name">Martin Hale</div>
      </div>
      <div class="card__body text">
        <p>Martin Hale is the Managing Director of Corvelle Advisory Pty Ltd.</p>
        <p>He has been providing financial planning and investment advice to clients since 1993. Prior to forming Corvelle Advisory, he has been director and part owner of Meridian Investment &amp; Retirement Services Pty Ltd since 1998.</p>
        <p>He holds a Bachelor of Business in Accounting &amp; Finance, a graduate diploma in Financial Planning and is an Accredited Super Fund Specialist Adviser. He is a member of the Planning Practitioners Guild (PPG), a Fellow of the Finance Institute and is a member of the Society of Wealth Advisers (SWA).</p>
      </div>
    </article>

    <article class="card" style="left:257px;top:96px;height:335px">
      <div class="card__head">
        <div class="card__photo" role="img" aria-label="Portrait photo of Daniel Foster outdoors" style="background:linear-gradient(160deg,#b7c6a8,#7d9163 55%,#283247)"></div>
        <div class="card__name">Daniel Foster</div>
      </div>
      <div class="card__body text">
        <p>Daniel Foster has been providing financial planning and investment advice to clients since 1999.</p>
        <p>He has five years specific financial planning and investment advice experience and an additional 10 years in banking and general insurance.</p>
        <p>He holds an Advanced Diploma in Financial Planning, a Diploma in Finance/Mortgage Broking and is currently working towards completing a Bachelor of Commerce at Westbrook University.</p>
        <p>Martin Hale, Peter Lazaridis and Daniel Foster will provide these services to you as Authorised Representatives of Corvelle Advisory Pty Ltd. They act on behalf of Corvelle Advisory Pty Ltd which is responsible for the services they provide.</p>
      </div>
    </article>

    <article class="card" style="left:20px;top:400px;height:226px">
      <div class="card__head">
        <div class="card__photo" role="img" aria-label="Portrait photo of Peter Lazaridis by the water" style="background:linear-gradient(160deg,#a9bccb,#7b8f70 55%,#34384a)"></div>
        <div class="card__name">Peter Lazaridis</div>
      </div>
      <div class="card__body text">
        <p>Peter Lazaridis chairs the investment committee of Corvelle Advisory Pty Ltd.</p>
        <p>He has many decades of experience in the financial services industry. He was Director Private Banking at Southgate Bank from 2009 to 2010 and was State Manager Broker Mortgage Services at Southgate Bank from 2005 to 2006. He also held a variety of senior positions within the Continental Bank of Australia where he served as an employee for over 30 years.</p>
      </div>
    </article>

    <article class="card" style="left:257px;top:476px;height:150px">
      <div class="card__body text" style="padding-top:14px">
        <p>He has extensive management and leadership skills and he holds a Diploma of Financial Planning from the Harbour Institute of Technology.</p>
      </div>
    </article>
  </div>
  <footer class="footer">Corvelle Advisory Pty Ltd &nbsp;•&nbsp; AFSL 000000 &nbsp;•&nbsp; ABN 00 000 000 000 &nbsp;&nbsp; www.corvelleadvisory.com.au
    <span class="footer__page">2</span></footer>
</section>

<section class="page page--right">
  <div class="panel">
    <div class="brand"><span class="brand__mark"></span><span class="brand__name">CORVELLE ADVISORY</span></div>
    <h2 class="section-title" style="left:19px">
      <svg viewBox="0 0 14 14"><circle cx="7" cy="7" r="6.2" fill="none" stroke="var(--brand-green)" stroke-width="1.2"/><path d="M6 4.3 8.6 7 6 9.7" fill="none" stroke="var(--brand-green)" stroke-width="1.3"/></svg>
      The financial advice process
    </h2>
    <h2 class="section-title" style="left:258px">
      <svg viewBox="0 0 14 14"><circle cx="7" cy="7" r="6.2" fill="none" stroke="var(--brand-green)" stroke-width="1.2"/><path d="M6 4.3 8.6 7 6 9.7" fill="none" stroke="var(--brand-green)" stroke-width="1.3"/></svg>
      Fees
    </h2>

    <div class="column text" style="left:19px;width:212px">
      <p>We recognise that the objectives and personal circumstances of each client are different.</p>
      <p>We understand that what is right for one client may not be right for another.</p>
      <p>We will listen to you to understand your objectives and circumstances. We will also ask questions to make sure we address all relevant issues.</p>
      <p>When we first provide advice to you it will be explained thoroughly and documented in a Statement of Advice which you can take away and study.</p>
      <p>The Statement of Advice will explain the basis for the advice, the cost to you of implementing the advice and any fees associated with the advice.</p>
      <p>For insurance and managed funds (except under the MDA service) recommendations, we will provide you with a Product Disclosure Statement. This contains information to help you understand the product being recommended.</p>
      <p>At all times you are able to contact us and ask questions about the advice and investments recommended.</p>
      <p>You can provide instructions to us in writing, via phone or via email/fax. Please note you are responsible for ensuring your instructions do actually reach us.</p>
      <p style="margin-bottom:0">We may provide further advice to you to keep your plan up to date with changes in your circumstances, changes in the law and changes in the economy and investments.</p>
      <p>The further advice we provide will be dependent on the Terms of Engagement you sign with us. It will be documented in a Record of Advice.</p>
    </div>

    <div class="column text fees" style="left:258px;width:214px">
      <p>All fees are payable to Corvelle Advisory Pty Ltd as Trustee for Harbourline Trust.</p>
      <p>Martin Hale is a beneficiary of Harbourline Trust and shares in the profits of the business.</p>
      <p>Peter Lazaridis and Daniel Foster are employees of Corvelle Advisory Pty Ltd as Trustee for Harbourline Trust. They will be paid a salary and may receive a performance bonus which amongst other items will be based on the revenue they generate for the business.</p>
      <p>Your first meeting with us is complimentary and obligation free.</p>
      <h4>Plan Preparation Fee</h4>
      <p>The Plan Preparation fee includes all meetings with you, the time we take to determine our advice and the production of the SoA.</p>
      <p>The Plan Preparation fee is based on the scope and complexity of advice provided to you. We will agree the fee with you at our first meeting or shortly after.</p>
      <h4>Plan Implementation Fee</h4>
      <p>If you decide to proceed with our advice we may charge a fee for the time we spend assisting you with implementation. We will let you know what the fee will be in the SoA.</p>
      <h4>Ongoing Services Fees</h4>
      <p>Once your investments are established we may provide you with ongoing services.</p>
      <p>Ongoing fees will depend on the services we provide to you. They may be a percentage of the transaction value, an agreed fixed fee or a percentage of your portfolio value.</p>
      <p>The services and fees will be set out in the SoA or RoA that we provide to you.</p>
    </div>
  </div>
  <footer class="footer">Corvelle Advisory Pty Ltd &nbsp;•&nbsp; AFSL 000000 &nbsp;•&nbsp; ABN 00 000 000 000 &nbsp;&nbsp; www.corvelleadvisory.com.au
    <span class="footer__page">3</span></footer>
</section>

</body>
</html>
```